Design a cover for a new book!

Design a cover for a new book called "Rivers Beneath Copper Fields" Subtitle is "Rebuilding Shared Prosperity Through Practical Industry Reform Plans"

The brief attached will give you the theme of the book. The book tells how there are two economies, one controlled by people who own financial assets, and the other run by people who build real things that contribute to our standard of living.

We want a split cover showing two different economies existing at the same time. The cover should show a split scene! Half the cover should be the monetary economy - the stock market or derivative or commodities. The other half the cover should show the material economy - technology and manufacturing, or maybe people living and doing things.

Target Market(s)

General Audience, people who like political policy

Industry/Entity Type

economics

Requirements
Must have
• The cover should show a split scene! Half the cover should be the monetary economy - the stock market or derivative or commodities. The other half the cover should show the material economy - technology and manufacturing,

```html
<!DOCTYPE html>
<html lang="en">
<head>
<meta charset="utf-8">
<title>Rivers Beneath Copper Fields — Book Cover</title>
<link rel="stylesheet" href="https://fonts.googleapis.com/css2?family=Lato:wght@400;700&family=Open+Sans:wght@300;400;700&display=swap">
<style>
  :root {
    --crimson: #b5123f;
    --paper: #ffffff;
    --ink-white: #ffffff;
    --market-deep: #1d2f7a;
    --market-mid: #5a4fb8;
    --market-glow: #6fd6ff;
    --factory-dark: #1b2230;
    --factory-mid: #3a4250;
    --factory-amber: #e0a030;
  }
  html, body { margin: 0; padding: 0; overflow: hidden; background: var(--paper); }
  .cover {
    position: relative; width: 1200px; height: 914px; overflow: hidden;
    background: var(--paper); font-family: "Lato", sans-serif;
  }
  .band { position: absolute; }
  .back-band { left: 0; top: 300px; width: 586px; height: 312px; background: var(--crimson); }
  .front-band { left: 612px; top: 300px; width: 588px; height: 332px; background: var(--crimson); }
  .market-art {
    position: absolute; left: 612px; top: 0; width: 588px; height: 312px;
    background: linear-gradient(110deg, #c9cfe0 0%, #8c96c4 35%, var(--market-mid) 60%, var(--market-deep) 85%),
                var(--market-deep);
  }
  .market-art::after {
    content: ""; position: absolute; inset: 0;
    background: radial-gradient(circle at 80% 30%, rgba(111,214,255,.55), transparent 55%);
  }
  .factory-art {
    position: absolute; left: 612px; top: 628px; width: 588px; height: 286px;
    background: radial-gradient(circle at 70% 15%, rgba(224,160,48,.75), transparent 45%),
                linear-gradient(180deg, var(--factory-mid), var(--factory-dark));
  }
  .edges { position: absolute; inset: 0; pointer-events: none; }

  .tagline {
    position: absolute; left: 54px; top: 58px; width: 500px; margin: 0;
    text-align: center; color: var(--crimson); font-weight: 700; font-size: 18.5px;
  }
  .blurb {
    position: absolute; left: 54px; top: 107px; width: 500px; margin: 0;
    color: var(--crimson); font-size: 16px; line-height: 21px; text-align: justify;
  }
  .blurb strong { font-weight: 700; }
  .endorsement {
    position: absolute; left: 54px; top: 346px; width: 500px; margin: 0;
    color: var(--ink-white); font-size: 17px; line-height: 21.5px; text-align: justify;
  }
  .endorser {
    position: absolute; right: 646px; top: 570px; margin: 0;
    color: var(--ink-white); font-size: 17px;
  }
  .author-photo {
    position: absolute; left: 51px; top: 628px; width: 99px; height: 124px;
    background: linear-gradient(180deg, #7b8a5a 0%, #c99a7a 50%, #8a2a30 100%);
  }
  .bio {
    position: absolute; left: 157px; top: 630px; width: 398px; margin: 0;
    color: var(--crimson); font-size: 16px; line-height: 20.5px; text-align: justify;
  }

  .spine-title, .spine-author {
    position: absolute; left: 588px; width: 22px; margin: 0;
    writing-mode: vertical-rl; color: var(--crimson);
    white-space: nowrap; text-align: center; line-height: 22px;
  }
  .spine-title { top: 326px; height: 290px; font-family: "Open Sans", sans-serif; font-size: 12.5px; letter-spacing: 1.5px; font-weight: 400; }
  .spine-title b { font-weight: 700; }
  .spine-author { top: 690px; height: 170px; font-size: 13px; font-weight: 700; letter-spacing: .5px; }

  .title {
    position: absolute; left: 612px; top: 340px; width: 588px; margin: 0;
    text-align: center; color: var(--ink-white); font-family: "Open Sans", sans-serif; line-height: 1.08;
  }
  .title .lead { display: block; font-weight: 300; font-size: 46px; }
  .title .main { display: block; font-weight: 700; font-size: 48px; }
  .subtitle {
    position: absolute; left: 660px; top: 470px; width: 490px; margin: 0;
    text-align: center; color: var(--ink-white); font-weight: 700; font-size: 23px; line-height: 31px;
  }
  .author {
    position: absolute; left: 612px; top: 566px; width: 588px; margin: 0;
    text-align: center; color: var(--ink-white); font-weight: 700; font-size: 33px; letter-spacing: .5px;
  }
</style>
</head>
<body>
<div class="cover">
  <div class="band back-band"></div>
  <div class="band front-band"></div>
  <div class="market-art" role="img" aria-label="Monetary economy artwork: banknote portrait overlaid with glowing stock market candlestick charts"></div>
  <div class="factory-art" role="img" aria-label="Material economy photograph: engineer with laptop beside yellow robotic arms on a factory line"></div>

  <svg class="edges" width="1200" height="914" viewBox="0 0 1200 914" aria-hidden="true">
    <g fill="#ffffff">
      <path d="M0,292 L0,302 L20,299 L40,304 L62,298 L85,303 L110,300 L132,305 L158,299 L180,303 L205,298 L230,304 L255,300 L280,305 L305,299 L330,303 L355,298 L380,304 L405,300 L430,305 L455,299 L480,303 L505,298 L530,304 L555,300 L586,303 L586,292 Z"/>
      <path d="M0,606 L22,610 L45,604 L70,611 L95,605 L120,610 L146,604 L170,611 L196,606 L222,610 L248,604 L272,611 L298,605 L324,610 L350,604 L376,611 L402,606 L428,610 L454,604 L480,611 L506,605 L532,610 L560,604 L586,609 L586,618 L0,618 Z"/>
      <path d="M612,304 L636,300 L660,306 L686,301 L712,307 L738,302 L764,306 L790,300 L816,307 L842,302 L868,306 L894,300 L920,307 L946,302 L972,306 L998,300 L1024,307 L1050,302 L1076,306 L1102,300 L1128,307 L1154,302 L1180,306 L1200,302 L1200,316 L1176,312 L1150,317 L1124,313 L1098,317 L1072,312 L1046,317 L1020,313 L994,317 L968,312 L942,317 L916,313 L890,317 L864,312 L838,317 L812,313 L786,317 L760,312 L734,317 L708,313 L682,317 L656,312 L630,317 L612,313 Z"/>
      <path d="M612,624 L638,628 L664,622 L690,629 L716,623 L742,628 L768,622 L794,629 L820,623 L846,628 L872,622 L898,629 L924,623 L950,628 L976,622 L1002,629 L1028,623 L1054,628 L1080,622 L1106,629 L1132,623 L1158,628 L1184,622 L1200,627 L1200,636 L1174,632 L1148,637 L1122,633 L1096,637 L1070,632 L1044,637 L1018,633 L992,637 L966,632 L940,637 L914,633 L888,637 L862,632 L836,637 L810,633 L784,637 L758,632 L732,637 L706,633 L680,637 L654,632 L628,637 L612,633 Z"/>
    </g>
  </svg>

  <p class="tagline">It is the best of times, it is the worst of times.</p>
  <p class="blurb"><strong>Rivers Beneath Copper Fields</strong> details the battle between the material and monetary economies. While the development of modern technology in our material economy has us on the brink of prosperity, a turf war in our monetary economy is destroying our prospects for enjoying this success. This book provides solutions to reverse the erosion of our standard of living caused by our monetary economy with an upgrade to our financial operating system that would benefit both rich and poor.</p>

  <p class="endorsement">“Whether you are a political pundit, economist, or Wall Street banker, Rivers Beneath Copper Fields is a must-read on what ails our nation today. This book sets the story straight on a battle between two economies and offers a stunning way out of our financial travails. The solution’s brilliance is in its simplicity. In one fell swoop, author Daniel Whitaker wipes out income taxes, balances the budget, and sets our nation on a path to paying off its national debt, while also affording new benefits that would catapult our nation into an era of unprecedented prosperity.”</p>
  <p class="endorser">—Marcus Halloran</p>

  <div class="author-photo" role="img" aria-label="Author portrait photograph"></div>
  <p class="bio">Daniel Whitaker is an early pioneer of structured finance and a serial entrepreneur, having co-founded software technology companies, charter schools, and an international publication for students. He enjoys painting galaxies and writing about the economy.</p>

  <p class="spine-title">RIVERS BENEATH <b>COPPER FIELDS</b></p>
  <p class="spine-author">DANIEL REED WHITAKER</p>

  <h1 class="title"><span class="lead">RIVERS BENEATH</span><span class="main">COPPER FIELDS</span></h1>
  <p class="subtitle">Rebuilding Shared Prosperity Through Practical Industry Reform Plans</p>
  <p class="author">DANIEL REED WHITAKER</p>
</div>
</body>
</html>
```